KRV Business Card

Looking for a business card for my restaurant group I own. Four different concepts:

Copperfield Alehouse
Bristow Alehouse
Tanager's Stone Hearth Kitchen
Pellston Patty Company

Card doesn't need to include all the logos.

```html
<!DOCTYPE html>
<html lang="en">
<head>
<meta charset="utf-8">
<title>KRV Business Card</title>
<link rel="stylesheet" href="https://fonts.googleapis.com/css2?family=Montserrat:wght@500;600&family=Lato:wght@400;700&display=swap">
<style>
  :root {
    --stage: #2a2a2a;
    --slate: #6e6f72;
    --gold: #cfad6a;
    --white: #ffffff;
    --ink: #5d5e61;
    --rule: #6a6a6a;
    --ghost: #f3f1ee;
  }
  * { box-sizing: border-box; margin: 0; padding: 0; }
  html, body { width: 1200px; height: 1200px; overflow: hidden; }
  body { background: var(--stage); position: relative; font-family: "Lato", sans-serif; }

  .card {
    position: absolute;
    left: 229px;
    width: 742px;
    height: 423px;
    border-radius: 22px;
    overflow: hidden;
  }
  .card--front { top: 153px; background: var(--slate); }
  .card--back { top: 623px; background: var(--white); }

  .brand { font-family: "Montserrat", sans-serif; font-weight: 500; color: var(--gold); text-transform: uppercase; }

  .front-brand {
    position: absolute; left: 0; right: 0; top: 78px; text-align: center;
  }
  .front-brand .brand-mark { display: block; font-size: 78px; letter-spacing: 6px; line-height: 1; }
  .front-brand .brand-name { display: block; font-size: 48px; letter-spacing: 4px; margin-top: 22px; line-height: 1; }
  .front-brand .brand-sub { display: block; font-size: 25px; letter-spacing: 3px; margin-top: 10px; line-height: 1; }

  .front-web {
    position: absolute; left: 0; right: 0; top: 357px; text-align: center;
    font-weight: 700; font-size: 19px; color: var(--white);
  }
  .front-web .accent { color: var(--gold); }

  .back-brand { position: absolute; left: 44px; top: 38px; width: 254px; text-align: center; }
  .back-brand .brand-mark { display: block; font-size: 62px; letter-spacing: 5px; line-height: 1; }
  .back-brand .brand-name { display: block; font-size: 38px; letter-spacing: 3px; margin-top: 14px; line-height: 1; }
  .back-brand .brand-sub { display: block; font-size: 20px; letter-spacing: 2px; margin-top: 8px; line-height: 1; }

  .ghost-mark {
    position: absolute; left: 466px; top: 40px;
    font-family: "Montserrat", sans-serif; font-weight: 500;
    font-size: 104px; letter-spacing: 6px; line-height: 1; color: var(--ghost);
  }

  .holder { position: absolute; right: 44px; top: 228px; text-align: right; }
  .holder-name {
    font-family: "Montserrat", sans-serif; font-weight: 600; font-size: 31px;
    letter-spacing: 1px; color: var(--gold); line-height: 1;
  }
  .holder-role { font-size: 20px; color: var(--ink); margin-top: 8px; line-height: 1; }

  .divider { position: absolute; left: 44px; top: 279px; width: 580px; height: 2px; background: var(--rule); }

  .contact-list { position: absolute; left: 44px; top: 300px; list-style: none; }
  .contact-list li {
    display: flex; align-items: center; gap: 12px;
    font-size: 20px; color: var(--ink); height: 29px;
  }
  .contact-list svg { width: 16px; height: 16px; fill: var(--gold); flex: none; }

  .address {
    position: absolute; right: 44px; top: 304px; text-align: right;
    font-size: 20px; color: var(--ink); line-height: 29px; font-style: normal;
  }

  .footer-band { position: absolute; left: 0; bottom: 0; width: 742px; height: 24px; }
</style>
</head>
<body>

  <section class="card card--front">
    <div class="front-brand brand">
      <span class="brand-mark">KRV</span>
      <span class="brand-name">Kestrel River</span>
      <span class="brand-sub">Hospitality</span>
    </div>
    <p class="front-web">www.<span class="accent">kestrelriverhospitality</span>.com</p>
  </section>

  <section class="card card--back">
    <div class="back-brand brand">
      <span class="brand-mark">KRV</span>
      <span class="brand-name">Kestrel River</span>
      <span class="brand-sub">Hospitality</span>
    </div>
    <div class="ghost-mark" aria-hidden="true">KRV</div>

    <div class="holder">
      <p class="holder-name">MARISA CALLOWAY</p>
      <p class="holder-role">Owner</p>
    </div>
    <div class="divider"></div>

    <ul class="contact-list">
      <li>
        <svg viewBox="0 0 24 24" aria-hidden="true"><path d="M6.6 10.8a15.1 15.1 0 0 0 6.6 6.6l2.2-2.2a1 1 0 0 1 1-.25 11.4 11.4 0 0 0 3.6.57 1 1 0 0 1 1 1V20a1 1 0 0 1-1 1A17 17 0 0 1 3 4a1 1 0 0 1 1-1h3.5a1 1 0 0 1 1 1c0 1.25.2 2.45.57 3.57a1 1 0 0 1-.25 1z"/></svg>
        555.204.7761
      </li>
      <li>
        <svg viewBox="0 0 24 24" aria-hidden="true"><path d="M2 5h20v14H2z M2 5l10 8 10-8" fill="none" stroke="#cfad6a" stroke-width="0"/><path d="M2 6.5l10 7 10-7V19H2z M2 5h20l-10 7z"/></svg>
        marisacalloway@mailbox.com
      </li>
      <li>
        <svg viewBox="0 0 24 24" aria-hidden="true"><path d="M12 2a10 10 0 1 0 0 20 10 10 0 0 0 0-20zm6.9 6h-2.9a15 15 0 0 0-1.4-3.6A8 8 0 0 1 18.9 8zM12 4c.8 1.2 1.5 2.5 1.9 4h-3.8c.4-1.5 1.1-2.8 1.9-4zM4.3 14a8 8 0 0 1 0-4h3.4a16 16 0 0 0 0 4zm.8 2h2.9c.3 1.3.8 2.5 1.4 3.6A8 8 0 0 1 5.1 16zM8 8H5.1a8 8 0 0 1 4.3-3.6C8.8 5.5 8.3 6.7 8 8zm4 12c-.8-1.2-1.5-2.5-1.9-4h3.8c-.4 1.5-1.1 2.8-1.9 4zm2.3-6H9.7a14 14 0 0 1 0-4h4.6a14 14 0 0 1 0 4zm.3 5.6c.6-1.1 1.1-2.3 1.4-3.6h2.9a8 8 0 0 1-4.3 3.6zm1.7-5.6a16 16 0 0 0 0-4h3.4a8 8 0 0 1 0 4z"/></svg>
        www.kestrelriverhospitality.com
      </li>
    </ul>

    <address class="address">
      48 Alder Row, Suite B<br>
      Leeds, UK 30114
    </address>

    <svg class="footer-band" viewBox="0 0 742 24" preserveAspectRatio="none" aria-hidden="true">
      <polygon points="0,0 472,0 452,24 0,24" fill="#6e6f72"/>
      <polygon points="484,0 742,0 742,24 464,24" fill="#cfad6a"/>
    </svg>
  </section>

</body>
</html>
```